National Sales - Pick Up Truck Dealer

We need a logo design for a new vehicle dealership based in Sydney, Australia. The business name is Coastal Iron Haulers Motor Co. We will be selling American 'trucks/pick up trucks' like KRV, Torvan, Blaxer, Morrow T420, Kenzo Raptors, Morrow T640 and the likes.

These vehicles are a luxury option and we would like the logo to be strong, luxurious and masculine.Colours will be black and red or black and blue with the option of grey and white.

Target Market(s)

Men

Industry/Entity Type

Car Dealer

Contact Information for Business Card

Dennis Harlowe
Managing Director
0412 639 274
den@qelvtrk.com.au

Level 3, Brindle Parkway
17 Pemberly Lane
Merriton Vale
WSR
Australia
Licence No: MD493152

Back of the card

qelvtrk.com.au

Font styles to use
Sans Serif

Colors

Designer to choose colors to be used in the design.

Requirements
Must have
• The company logo that is in the attachments, you can choose from the three which one you would like to work with. Must have vehicle images ....Please look at the attachments as they show examples of what we like and also provides potential images. If you choose to put an image on the front even if it is just the front of the vehicle can you please use the Black KRV Sorrento. Must have all details from the business card details section front and back
Nice to have
• N/A
Should not have
• No cars or standard trucks, please refer to the attached images to understand the product . Should not have any new logos or branding. No other colours besides what is in the logo you choose.

```html
<!DOCTYPE html>
<html lang="en">
<head>
<meta charset="utf-8">
<title>Coastal Iron Haulers Motor Co – Business Card</title>
<link rel="stylesheet" href="https://fonts.googleapis.com/css2?family=Exo+2:wght@700;800&family=Montserrat:wght@500;700&display=swap">
<style>
  :root {
    --bg: #2a2a2c;
    --card-dark: #1f1d1e;
    --card-light: #ffffff;
    --red: #b3212b;
    --white: #ffffff;
    --ink: #1c1c1e;
  }
  * { box-sizing: border-box; margin: 0; padding: 0; }
  html, body { width: 1200px; height: 880px; overflow: hidden; }
  body {
    background: var(--bg);
    font-family: "Montserrat", sans-serif;
    position: relative;
  }
  .card {
    position: absolute;
    left: 250px;
    width: 700px;
    height: 400px;
    border-radius: 22px;
    overflow: hidden;
    background: var(--card-dark);
    box-shadow: 0 14px 30px rgba(0,0,0,.45);
  }
  .card--front { top: 25px; }
  .card--back { top: 455px; }

  .brand-name {
    position: absolute;
    font-family: "Exo 2", sans-serif;
    font-weight: 800;
    text-transform: uppercase;
    line-height: 1.05;
    letter-spacing: .5px;
  }
  .card--front .brand-name {
    left: 44px; top: 92px; width: 280px;
    font-size: 34px; color: var(--white);
  }
  .truck-photo {
    position: absolute;
    right: 0; top: 0;
    width: 380px; height: 290px;
    background: radial-gradient(ellipse at 55% 50%, #5a5a5e 0%, #2c2c2f 45%, var(--card-dark) 75%);
  }
  .front-phone {
    position: absolute;
    left: 44px; top: 272px;
    font-family: "Exo 2", sans-serif;
    font-weight: 800;
    font-size: 34px;
    color: var(--white);
    letter-spacing: 1px;
  }
  .front-web {
    position: absolute;
    left: 46px; top: 325px;
    font-size: 18px;
    color: var(--white);
    letter-spacing: 3px;
  }

  .back-shape { position: absolute; inset: 0; }
  .card--back .brand-name {
    left: 40px; top: 150px; width: 320px;
    font-size: 30px; color: var(--ink);
  }
  .contact {
    position: absolute;
    left: 452px; top: 46px;
    width: 240px;
    color: var(--white);
    font-size: 13px;
    line-height: 1.45;
  }
  .contact__name {
    font-family: "Exo 2", sans-serif;
    font-weight: 800;
    font-size: 22px;
    line-height: 1.1;
  }
  .contact__role {
    color: var(--red);
    font-weight: 700;
    font-size: 15px;
    margin-bottom: 14px;
  }
  .contact__line { display: flex; align-items: center; gap: 7px; }
  .contact__icon {
    width: 15px; height: 15px; border-radius: 50%;
    background: var(--red);
    display: inline-flex; align-items: center; justify-content: center;
    flex: none;
  }
  .contact__address { margin-top: 16px; }
  .contact__web { margin-top: 22px; letter-spacing: 2px; font-size: 14px; }
</style>
</head>
<body>

  <section class="card card--front">
    <div class="brand-name">Coastal Iron Haulers Motor Co</div>
    <div class="truck-photo" role="img" aria-label="Photo of the front of a black KRV Sorrento pickup truck with chrome grille"></div>
    <div class="front-phone">0412 639 274</div>
    <div class="front-web">www.qelvtrk.com.au</div>
  </section>

  <section class="card card--back">
    <svg class="back-shape" viewBox="0 0 700 400" aria-hidden="true">
      <path d="M0,0 L230,0 C375,40 450,190 415,400 L0,400 Z" fill="var(--card-light)"/>
      <path d="M245,0 C395,35 470,190 432,400 L415,400 C450,190 375,40 230,0 Z" fill="var(--red)"/>
    </svg>
    <div class="brand-name">Coastal Iron Haulers Motor Co</div>
    <div class="contact">
      <div class="contact__name">Dennis Harlowe</div>
      <div class="contact__role">Managing Director</div>
      <div class="contact__line">
        <span class="contact__icon">
          <svg width="7" height="10" viewBox="0 0 7 10"><rect x="0.8" y="0.5" width="5.4" height="9" rx="1" fill="none" stroke="#fff" stroke-width="1"/></svg>
        </span>0412 639 274
      </div>
      <div class="contact__line">
        <span class="contact__icon">
          <svg width="9" height="7" viewBox="0 0 9 7"><rect x="0.5" y="0.5" width="8" height="6" fill="none" stroke="#fff" stroke-width="1"/><path d="M0.5,0.5 L4.5,4 L8.5,0.5" fill="none" stroke="#fff" stroke-width="1"/></svg>
        </span>den@qelvtrk.com.au
      </div>
      <div class="contact__address">
        Level 3, Brindle Parkway<br>
        17 Pemberly Lane<br>
        Merriton Vale, WSR<br>
        Australia
      </div>
      <div class="contact__web">www.qelvtrk.com.au</div>
    </div>
  </section>

</body>
</html>
```